Business Card Design for Online Gift Business

Business card design for a new online Canadian company called "Harlow & Brine Gift Boxes" selling modern and luxurious gift boxes for every occasion. Items are sourced locally from talented socially-responsible Canadian artisans. Each gift is elegantly presented in a keepsake wood box to ensure a lasting impression.

Industry/Entity Type

E-Commerce

Contact Information for Business Card

Marla Whitcombe, Proprietor
Larchmere, AB
403-555-2741
www.harlowandbrine.ca
hello@harlowandbrine.ca

Requirements
Must have
• Made with care, given with heart
• Please also include the symbols for Facebook and Instagram
Nice to have
• **I have attached a few samples of background colors and font colors that I like. I hope this helps in a few directions to try.

```html
<!DOCTYPE html>
<html lang="en">
<head>
<meta charset="utf-8">
<title>Harlow &amp; Brine Gift Boxes – Business Card</title>
<link href="https://fonts.googleapis.com/css2?family=Pinyon+Script&family=Cormorant+Garamond:wght@500&family=Dosis:wght@500&display=swap" rel="stylesheet">
<style>
  :root {
    --backdrop: #a9b0b2;
    --card: #e8c6ac;
    --ink: #4b2a16;
    --rule: #6b4a34;
  }
  * { box-sizing: border-box; margin: 0; padding: 0; }
  html, body {
    width: 1200px;
    height: 824px;
    overflow: hidden;
    background: var(--backdrop);
  }
  .stage {
    width: 1200px;
    height: 824px;
    display: flex;
    align-items: center;
    justify-content: center;
    gap: 50px;
  }
  .card {
    width: 525px;
    height: 300px;
    background: var(--card);
    color: var(--ink);
    position: relative;
    display: flex;
    flex-direction: column;
    align-items: center;
    justify-content: center;
  }

  /* Contact side */
  .back-mark {
    width: 26px;
    height: 26px;
    border-radius: 50%;
    background: var(--ink);
    margin-bottom: 14px;
  }
  .person-name {
    font-family: "Pinyon Script", cursive;
    font-weight: 400;
    font-size: 44px;
    line-height: 1.1;
  }
  .person-role {
    font-family: "Pinyon Script", cursive;
    font-size: 22px;
    line-height: 1.2;
    margin-top: 2px;
    margin-bottom: 10px;
  }
  .contact-line {
    width: 400px;
    border-top: 1px dotted var(--rule);
    border-bottom: 1px dotted var(--rule);
    padding: 6px 0;
    text-align: center;
    font-family: "Dosis", sans-serif;
    font-weight: 500;
    font-size: 15px;
    letter-spacing: 0.04em;
    text-transform: uppercase;
    white-space: nowrap;
  }
  .contact-line .sep { margin: 0 6px; }
  .social-row {
    display: flex;
    gap: 6px;
    margin-top: 8px;
  }
  .social-dot {
    width: 17px;
    height: 17px;
    border-radius: 50%;
    border: 1.5px solid var(--ink);
  }

  /* Brand side */
  .brand-name {
    font-family: "Cormorant Garamond", serif;
    font-weight: 500;
    font-size: 44px;
    letter-spacing: 0.14em;
    text-transform: uppercase;
    line-height: 1;
  }
  .brand-sub {
    font-family: "Cormorant Garamond", serif;
    font-weight: 500;
    font-size: 16px;
    letter-spacing: 0.5em;
    text-transform: uppercase;
    margin-top: 10px;
  }
  .tagline {
    font-family: "Pinyon Script", cursive;
    font-size: 26px;
    margin-top: 26px;
  }
</style>
</head>
<body>
  <main class="stage">
    <section class="card card-back" aria-label="Business card, contact side">
      <div class="back-mark" aria-hidden="true"></div>
      <h1 class="person-name">Marla Whitcombe</h1>
      <p class="person-role">Proprietor</p>
      <p class="contact-line">Larchmere, AB<span class="sep">|</span>403-555-2741<span class="sep">|</span>www.harlowandbrine.ca</p>
      <div class="social-row">
        <span class="social-dot" role="img" aria-label="Social profile"></span>
        <span class="social-dot" role="img" aria-label="Social profile"></span>
      </div>
    </section>

    <section class="card card-front" aria-label="Business card, brand side">
      <h2 class="brand-name">Harlow &amp; Brine</h2>
      <p class="brand-sub">Gift Boxes</p>
      <p class="tagline">Made with care, given with heart</p>
    </section>
  </main>
</body>
</html>
```